KDWB Business Card

Looking for a business card design to incorporate our branding. We want to only use the colors listing in the Branding Package (attached).
Updates

Target Market(s)

People who need their phone or device fixed.

Industry/Entity Type

Electronics

Contact Information for Business Card

Please use:

Brightwick Gadget Clinic LLC
4810 E Harlow Ridge Rd
Suite 417
San Antonio, TX 78163

Marcus Delgrove, Store Manager

(210) 555-0147

Requirements
Must have
• Must include the colors that are contained within the Branding Package PDF file.

```html
<!DOCTYPE html>
<html lang="en">
<head>
<meta charset="utf-8">
<title>Brightwick Gadget Clinic — Business Card</title>
<link rel="stylesheet" href="https://fonts.googleapis.com/css2?family=Open+Sans:wght@400;600&display=swap">
<style>
  :root {
    --backdrop: #3a3431;
    --card: #121212;
    --card-edge: #1c1c1c;
    --orange: #ff5a00;
    --white: #f2f2f2;
    --grey: #bdbdbd;
  }
  * { margin: 0; padding: 0; box-sizing: border-box; }
  html, body { width: 1200px; height: 844px; overflow: hidden; }
  body {
    background: var(--backdrop);
    font-family: "Open Sans", Arial, sans-serif;
    position: relative;
  }
  .card {
    position: absolute;
    width: 540px;
    height: 309px;
    background: var(--card);
    border: 1px solid var(--card-edge);
    border-radius: 4px;
    box-shadow: 0 10px 30px rgba(0,0,0,.45);
    top: 268px;
  }
  .card--front { left: 30px; }
  .card--back { left: 630px; }

  .brand {
    position: absolute;
    display: flex;
    align-items: center;
    gap: 14px;
  }
  .brand__mark {
    width: 46px; height: 46px;
    background: var(--orange);
    border-radius: 8px;
    flex: none;
  }
  .brand__name {
    color: var(--orange);
    font-weight: 400;
    font-size: 27px;
    line-height: 1.1;
    white-space: nowrap;
  }
  .card--front .brand { left: 60px; top: 64px; }
  .card--back .brand { left: 50%; top: 50%; transform: translate(-50%, -50%); }

  .company {
    position: absolute;
    left: 40px;
    bottom: 40px;
    color: var(--white);
    font-size: 15px;
    line-height: 1.5;
  }
  .company__name { color: var(--orange); font-weight: 600; }

  .contact {
    position: absolute;
    right: 36px;
    top: 150px;
    text-align: right;
    color: var(--white);
  }
  .contact__name { color: var(--orange); font-weight: 600; font-size: 17px; }
  .contact__role { font-size: 12px; margin-top: 2px; }
  .contact__phone {
    font-size: 13px;
    margin-top: 8px;
    display: flex;
    align-items: center;
    justify-content: flex-end;
    gap: 6px;
  }
  .contact__phone svg { width: 11px; height: 11px; fill: var(--orange); }
</style>
</head>
<body>
  <section class="card card--front" aria-label="Business card front">
    <div class="brand">
      <span class="brand__mark"></span>
      <span class="brand__name">Brightwick Gadget Clinic</span>
    </div>

    <div class="contact">
      <p class="contact__name">Marcus Delgrove</p>
      <p class="contact__role">Store Manager</p>
      <p class="contact__phone">(210) 555-0147
        <svg viewBox="0 0 24 24" aria-hidden="true"><path d="M6.6 10.8a15.1 15.1 0 0 0 6.6 6.6l2.2-2.2c.3-.3.7-.4 1-.2 1.1.4 2.3.6 3.6.6.6 0 1 .4 1 1V20c0 .6-.4 1-1 1A17 17 0 0 1 3 4c0-.6.4-1 1-1h3.5c.6 0 1 .4 1 1 0 1.3.2 2.5.6 3.6.1.3 0 .7-.2 1z"/></svg>
      </p>
    </div>

    <address class="company" style="font-style:normal">
      <p class="company__name">Brightwick Gadget Clinic LLC</p>
      <p>4810 E Harlow Ridge Rd Suite</p>
      <p>417 San Antonio, TX 78163</p>
    </address>
  </section>

  <section class="card card--back" aria-label="Business card back">
    <div class="brand">
      <span class="brand__mark"></span>
      <span class="brand__name">Brightwick Gadget Clinic</span>
    </div>
  </section>
</body>
</html>
```